Wordpress Website design partner needed for an Arabic Language Institute for English Speakers

We are an online Arabic Language institute, targeting English Speakers around the world and we provide online courses and private group and one on one classes
We are looking for a total of 5 pages designed.
The Design should be mobile-first, and then provide PC for any differences.
I am looking for a consistent design with a lot of white space and in line with our Logo colours.
Images used should be around the theme of Arabic Language/Islamic in Nature, so please do not use any illustrations or images of animals or human beings except for silhouettes or images without faces visible, such as someone facing other way or below torso or hands etc.
The website will eventually be prepared for Wordpress using Divi.
I will provide a very structured outline of what elements and modules each page should have. Therefore I am looking for someone that has an eye for detail and is precise in executing requirements.
I decided to post on this site because I am looking for a long-term partner that can take care of any of our design needs as they come up.
More details to follow
I will do abit more research tomorrow to suggest sample sites
Updates
Target Market(s)
English speakers that want to learn Arabic for Religous purposes such as understanding the Quran
Industry/Entity Type
Education
Colors
Designer to choose colors to be used in the design.
Requirements
Must have
- Mobile First, and design for PC for changes
- Consistency
- Plenty of White Space
- Colour Palette based on Logo
- Colour and Transparent/White Header for when scrolling
- Big Call to Action buttons with contrasting colors
- A consistent footer for all pages with
- -Social Media Icons
- -Contact us
- -Sitemap
- -Copyright
- -Logo
- Anything with a hashtag (#) beforehand in the Doc file means it should be a module like the modules used in Divi Theme, Please check the following website for an explanation of what each module consists of and some examples of it in use. https://www.pelmorashowcase.net/pelmora-blocks-guide/
Nice to have
- Parallax Effect
Should not have
- illustrations or images of animals or human beings except for silhouettes or images without faces visible, such as someone facing other way or below torso or hands etc.

```html
<!DOCTYPE html>
<html lang="en">
<head>
<meta charset="utf-8">
<title>Al-Nour Arabic Academy</title>
<link href="https://fonts.googleapis.com/css2?family=IBM+Plex+Sans:wght@400;500;600&display=swap" rel="stylesheet">
<style>
:root{
  --blue:#0f4a9a;
  --blue-deep:#0a3a80;
  --teal:#2596a8;
  --ink:#222;
  --text:#333;
  --mist:#f4f0f1;
  --footer:#222222;
  --white:#fff;
  --muted:#ccc;
}
*{margin:0;padding:0;box-sizing:border-box}
html,body{width:706px;height:1200px;overflow:hidden}
body{font-family:"IBM Plex Sans",Arial,sans-serif;color:var(--text);background:var(--white);position:relative}

/* header */
.hero{position:absolute;left:0;top:0;width:706px;height:216px;background:var(--blue);overflow:hidden}
.hero-backdrop{position:absolute;left:0;top:60px;width:620px;height:156px;background:linear-gradient(90deg,rgba(10,58,128,.55) 0%,rgba(10,58,128,.35) 45%,rgba(15,74,154,0) 100%)}
.nav-link{position:absolute;top:44px;color:var(--white);font-size:8.8px;font-weight:500;letter-spacing:.2px}
.nav-divider{position:absolute;top:40px;width:1px;height:18px;background:var(--white)}
.brand{position:absolute;left:318px;top:38px;width:70px;text-align:center;color:var(--white);font-size:9px;font-weight:600;letter-spacing:.6px;line-height:1.25}
.login{position:absolute;left:572px;top:38px;width:55px;height:23px;border:1.5px solid var(--white);border-radius:12px;color:var(--white);font-size:8px;font-weight:600;text-align:center;line-height:20px}
.hero-title{position:absolute;left:0;top:117px;width:706px;text-align:center;color:var(--white);font-size:15.8px;font-weight:600;line-height:24px;letter-spacing:.1px}

/* intro */
.intro-title{position:absolute;left:0;top:247px;width:706px;text-align:center;color:var(--ink);font-size:13.8px;font-weight:500}
.intro-text{position:absolute;left:176px;top:274px;width:356px;text-align:center;font-size:8px;line-height:12.3px}
.video{position:absolute;left:134px;top:316px;width:438px;height:225px;background:radial-gradient(ellipse at 60% 50%,#c9a878 0%,#7a5534 35%,#3c2a22 75%,#2a2220 100%)}
.play{position:absolute;left:205px;top:98px}
.btn{position:absolute;background:var(--teal);color:var(--white);font-weight:600;text-align:center}
.btn-watch{left:302px;top:564px;width:102px;height:30px;border-radius:15px;font-size:9.8px;line-height:30px}

/* about */
.about{position:absolute;left:0;top:632px;width:706px;height:334px;background:var(--mist)}
.about-photo{position:absolute;left:76px;top:32px;width:263px;height:267px;background:linear-gradient(135deg,#8f8c85 0%,#3b5a73 40%,#6d6a58 70%,#9d9a87 100%)}
.about-title{position:absolute;left:362px;top:29px;color:var(--ink);font-size:13.8px;font-weight:600}
.about-text{position:absolute;left:363px;top:60px;width:264px;font-size:8.1px;line-height:12.3px}
.checklist{position:absolute;left:365px;top:177px;list-style:none;font-size:8.2px}
.checklist li{height:16.5px;display:flex;align-items:center}
.checklist svg{margin-right:8px}
.btn-more{left:365px;top:278px;width:69px;height:23px;border-radius:12px;font-size:7.6px;line-height:23px}

/* footer */
.footer{position:absolute;left:0;top:966px;width:706px;height:234px;background:var(--footer);color:var(--white)}
.f-head{position:absolute;top:33px;font-size:8px;font-weight:500;letter-spacing:.2px}
.icon-dot{position:absolute;border-radius:50%;background:var(--teal);display:flex;align-items:center;justify-content:center}
.contact-line{position:absolute;left:107px;font-size:7.4px;font-weight:500;line-height:10px}
.contact-line b{font-weight:600;font-size:8.2px}
.frame-line{position:absolute;background:#bbb}
.f-brand{position:absolute;left:300px;top:116px;width:106px;text-align:center}
.f-brand .name{font-size:11px;font-weight:600;letter-spacing:2.2px;line-height:12px}
.f-brand .sub{font-size:5.4px;font-weight:600;letter-spacing:2px;margin-top:2px}
.f-nav{position:absolute;top:151px;font-size:8.2px;font-weight:500}
.social-line{position:absolute;left:550px;font-size:8px;line-height:11.5px;color:#e8e8e8}
.f-rule{position:absolute;left:77px;top:186px;width:552px;height:1px;background:#555}
.copyright{position:absolute;left:0;top:206px;width:696px;text-align:center;font-size:6.8px;color:var(--muted)}
</style>
</head>
<body>

<header class="hero">
  <div class="hero-backdrop" role="img" aria-label="Mosque domes and minarets silhouette in deep blue"></div>
  <span class="nav-link" style="left:185px">HOME</span>
  <span class="nav-divider" style="left:231px"></span>
  <span class="nav-link" style="left:247px">ABOUT US</span>
  <div class="brand">AL-NOUR<br>ACADEMY</div>
  <span class="nav-link" style="left:406px">COURSES</span>
  <span class="nav-divider" style="left:463px"></span>
  <span class="nav-link" style="left:480px">CONTACT US</span>
  <span class="login">LOGIN</span>
  <h1 class="hero-title">LOREM IPSUM DOLOR SIT AMET CONSECTETUR<br>ADIPISCING ELIT SED DO EIUSMOD.</h1>
</header>

<section>
  <h2 class="intro-title">AT VERO EOS ET ACCUSAMUS ET IUSTO ODIO</h2>
  <p class="intro-text">Lorem Ipsum is simply dummy text of the printing and typesetting industry. Lorem Ipsum has been the industry's standard dummy text ever since the 1500s when.</p>
  <div class="video" role="img" aria-label="Open Quran on a wooden stand over a prayer rug">
    <svg class="play" width="28" height="28" viewBox="0 0 28 28"><circle cx="14" cy="14" r="13" fill="#fff" fill-opacity=".9"/><path d="M11 8.5 L20 14 L11 19.5 Z" fill="#333"/></svg>
  </div>
  <span class="btn btn-watch">WATCH VIDEO</span>
</section>

<section class="about">
  <div class="about-photo" role="img" aria-label="Person in a headscarf, seen from behind, reading the Quran on a prayer rug"></div>
  <h2 class="about-title">ABOUT THIS COURSE</h2>
  <p class="about-text">When our power of choice is untrammelled and when nothing prevents our being able to do what we like best, every pleasure is to be welcomed and every pain avoided. But in certain circumstances and owing to the claims of duty or the obligations of business it will frequently occur that pleasures have to be repudiated and annoy ances accepted. The wise man therefore always holds in these matt ers to this principle of selection: he rejects pleasures to secure other greater pleasures.</p>
  <ul class="checklist">
    <li><svg width="8" height="7" viewBox="0 0 8 7"><path d="M1 3.6 L3 5.6 L7 1" stroke="var(--teal)" stroke-width="1.6" fill="none"/></svg>Sed ut perspiciatis unde omnis iste natus</li>
    <li><svg width="8" height="7" viewBox="0 0 8 7"><path d="M1 3.6 L3 5.6 L7 1" stroke="var(--teal)" stroke-width="1.6" fill="none"/></svg>But I must explain to you how all this mistake</li>
    <li><svg width="8" height="7" viewBox="0 0 8 7"><path d="M1 3.6 L3 5.6 L7 1" stroke="var(--teal)" stroke-width="1.6" fill="none"/></svg>At vero eos et accusamus et iusto</li>
    <li><svg width="8" height="7" viewBox="0 0 8 7"><path d="M1 3.6 L3 5.6 L7 1" stroke="var(--teal)" stroke-width="1.6" fill="none"/></svg>When our power of choice is untram</li>
    <li><svg width="8" height="7" viewBox="0 0 8 7"><path d="M1 3.6 L3 5.6 L7 1" stroke="var(--teal)" stroke-width="1.6" fill="none"/></svg>Quis nostrum exercitationem</li>
  </ul>
  <span class="btn btn-more">READ MORE</span>
</section>

<footer class="footer">
  <h3 class="f-head" style="left:80px">CONTACT US</h3>
  <span class="icon-dot" style="left:78px;top:60px;width:20px;height:20px">
    <svg width="9" height="9" viewBox="0 0 10 10"><path d="M2.2 1 L3.8 1 L4.4 3 L3.3 3.8 Q4.2 5.8 6.2 6.7 L7 5.6 L9 6.2 L9 7.8 Q9 9 7.8 9 Q1 8.6 1 2.2 Q1 1 2.2 1 Z" fill="#fff"/></svg>
  </span>
  <p class="contact-line" style="top:58px">CALL US<br><b>888.888.8888</b></p>
  <span class="icon-dot" style="left:78px;top:102px;width:20px;height:20px">
    <svg width="9" height="7" viewBox="0 0 10 8"><rect x="0.5" y="0.5" width="9" height="7" rx="1" fill="#fff"/><path d="M1 1.2 L5 4.4 L9 1.2" stroke="var(--teal)" stroke-width="1" fill="none"/></svg>
  </span>
  <p class="contact-line" style="top:100px">E MAIL US<br><b>info@alnouracademy.com</b></p>

  <span class="frame-line" style="left:252px;top:33px;width:1px;height:99px"></span>
  <span class="frame-line" style="left:252px;top:132px;width:56px;height:1px"></span>
  <span class="frame-line" style="left:454px;top:33px;width:1px;height:99px"></span>
  <span class="frame-line" style="left:397px;top:132px;width:58px;height:1px"></span>
  <div class="f-brand"><div class="name">AL-NOUR</div><div class="sub">ARABIC ACADEMY</div></div>

  <span class="f-nav" style="left:251px">HOME</span>
  <span class="f-nav" style="left:285px">ABOUT US</span>
  <span class="f-nav" style="left:336px">OUR COURSES</span>
  <span class="f-nav" style="left:404px">CONTACT US</span>

  <h3 class="f-head" style="left:526px">FOLLOW US</h3>
  <span class="icon-dot" style="left:525px;top:64px;width:17px;height:17px">
    <svg width="7" height="7" viewBox="0 0 8 8"><path d="M1.5 6.5 L6.5 1.5 M3 1.5 H6.5 V5" stroke="#fff" stroke-width="1.3" fill="none"/></svg>
  </span>
  <p class="social-line" style="top:61px">Like us on<br>CIRCLEBOOK</p>
  <span class="icon-dot" style="left:525px;top:101px;width:17px;height:17px">
    <svg width="7" height="7" viewBox="0 0 8 8"><path d="M1.5 6.5 L6.5 1.5 M3 1.5 H6.5 V5" stroke="#fff" stroke-width="1.3" fill="none"/></svg>
  </span>
  <p class="social-line" style="top:98px">Follow us on<br>CHIRPER</p>
  <span class="icon-dot" style="left:525px;top:137px;width:17px;height:17px">
    <svg width="7" height="7" viewBox="0 0 8 8"><path d="M1.5 6.5 L6.5 1.5 M3 1.5 H6.5 V5" stroke="#fff" stroke-width="1.3" fill="none"/></svg>
  </span>
  <p class="social-line" style="top:134px">Follow us on<br>LINKWORK</p>

  <span class="f-rule"></span>
  <p class="copyright">Copyright © 2020 All Rights Reserved</p>
</footer>

</body>
</html>
```